Business Card Design

We are a commercial real estate brokerage in San Francisco, leasing office buildings downtown.
I would like a clean, elegant look. Simple but powerful .

Industry/Entity Type

Business

Contact Information for Business Card

Derek Holloway
lic# 07258143
415.555.0172
derek@velt-commercial.example
velt-commercial.example

```html
<!DOCTYPE html>
<html lang="en">
<head>
<meta charset="utf-8">
<title>Velt Commercial — Business Card</title>
<link rel="stylesheet" href="https://fonts.googleapis.com/css2?family=Open+Sans:wght@400;600&display=swap">
<style>
  :root {
    --page-bg: #e9e7e3;
    --card-bg: #ffffff;
    --slate-blue: #7b8dab;
    --corner-dark: #4b4d50;
    --text-grey: #6b6b6b;
    --rule-grey: #8a8a8a;
    --art-light: #c9cacc;
    --art-dark: #7a7c80;
  }
  * { margin: 0; padding: 0; box-sizing: border-box; }
  html, body {
    width: 1200px; height: 950px; overflow: hidden;
    background: var(--page-bg);
    font-family: "Open Sans", Arial, sans-serif;
  }
  .sheet {
    position: relative; width: 1200px; height: 950px;
    display: flex; flex-direction: column; align-items: center; justify-content: center; gap: 50px;
  }
  .card {
    position: relative; width: 700px; height: 400px;
    background: var(--card-bg);
    box-shadow: 0 4px 14px rgba(0,0,0,0.18);
    overflow: hidden;
  }
  .card-corner { position: absolute; top: 0; right: 0; width: 70px; height: 26px; }

  /* front */
  .front-skyline {
    position: absolute; left: 235px; top: 80px; width: 230px; height: 130px;
    background: linear-gradient(180deg, var(--art-light), var(--art-dark));
  }
  .front-tagline {
    position: absolute; left: 0; right: 0; top: 240px;
    text-align: center; color: var(--text-grey); font-size: 15px; line-height: 1.45;
  }

  /* back */
  .brand {
    position: absolute; left: 70px; top: 118px;
    display: flex; align-items: center; gap: 16px;
  }
  .brand-skyline {
    width: 120px; height: 72px;
    background: linear-gradient(180deg, var(--art-light), var(--art-dark));
  }
  .brand-rule { width: 2px; height: 84px; background: var(--rule-grey); }
  .brand-name {
    color: var(--slate-blue); font-weight: 600; line-height: 1;
  }
  .brand-name .word-main { display: block; font-size: 46px; letter-spacing: 1px; }
  .brand-name .word-sub { display: block; font-size: 20px; letter-spacing: 1.5px; margin-top: 4px; }
  .person-name {
    position: absolute; right: 60px; top: 150px;
    color: var(--slate-blue); font-size: 19px; letter-spacing: 0.5px;
  }
  .contact {
    position: absolute; left: 70px; bottom: 42px;
    list-style: none; color: var(--text-grey); font-size: 15px; line-height: 1.55;
  }
</style>
</head>
<body>
<main class="sheet">
  <section class="card card-front">
    <svg class="card-corner" viewBox="0 0 70 26" aria-hidden="true"><polygon points="0,0 70,0 70,26" fill="var(--slate-blue)"/></svg>
    <div class="front-skyline" role="img" aria-label="Greyscale illustration of downtown office towers"></div>
    <p class="front-tagline">commercial real estate brokerage in San Francisco<br>leasing office buildings downtown.</p>
  </section>

  <section class="card card-back">
    <svg class="card-corner" viewBox="0 0 70 26" aria-hidden="true"><polygon points="0,0 70,0 70,26" fill="var(--corner-dark)"/></svg>
    <div class="brand">
      <div class="brand-skyline" role="img" aria-label="Small greyscale illustration of office towers"></div>
      <div class="brand-rule"></div>
      <div class="brand-name"><span class="word-main">VELT</span><span class="word-sub">COMMERCIAL</span></div>
    </div>
    <p class="person-name">DEREK HOLLOWAY</p>
    <ul class="contact">
      <li>lic# 07258143</li>
      <li>PH : 415.555.0172</li>
      <li>derek@velt-commercial.example</li>
      <li>velt-commercial.example</li>
    </ul>
  </section>
</main>
</body>
</html>
```